Website design for company that sells taximeters and has a taxi dispatch call center, webstore neede

Need a website with a shop with at least 20 articles, in two languages, possibly by using a purchased theme (not purchased yet).The company provides equipments and dispatch solutions for taxi companies. Typical yellow and black theme

Target Market(s)

Taxi companies

Industry/Entity Type

Taxi

Number of Pages Required

3 page

Font styles to use
Sans Serif

Colors
fbed22
000000

Requirements
Must have
• - webstore for at least 20 articles
• - Documents folder where to put pdf material related to taximeters
• - contact form message submission
Nice to have
• Feedback section
Should not have
• Blogs,

```html
<!DOCTYPE html>
<html lang="en">
<head>
<meta charset="utf-8">
<title>Fareway — Join Us</title>
<link rel="stylesheet" href="https://fonts.googleapis.com/css2?family=Lato:wght@400;700;900&family=Montserrat:wght@600;700;800&display=swap">
<style>
:root{
  --yellow:#f2c53d;
  --brand-yellow:#fbd022;
  --ink:#2e2e2e;
  --muted:#6b6b6b;
  --line:#c9c9c9;
  --black:#0b0b0b;
  --white:#ffffff;
}
*{box-sizing:border-box;margin:0;padding:0}
html,body{width:850px;height:1200px;overflow:hidden;background:var(--white)}
body{position:relative;font-family:'Lato',sans-serif;color:var(--ink)}
.abs{position:absolute}

/* hero */
.hero{left:0;top:0;width:850px;height:202px;
  background:radial-gradient(ellipse 160px 90px at 180px 130px,#6b5a1e 0%,#3a3016 45%,transparent 100%),
             linear-gradient(100deg,#1c1814 0%,#231d18 45%,#3a2a25 75%,#2a2a33 100%)}
.brand{left:106px;top:10px;font-family:'Montserrat',sans-serif;font-weight:800;font-size:17px;letter-spacing:1px;color:var(--brand-yellow)}
.nav{left:271px;top:15px;display:flex;gap:5px;font-family:'Montserrat',sans-serif;font-weight:700;font-size:7px;letter-spacing:.3px;color:var(--white)}
.nav .active{color:var(--brand-yellow)}
.phone{left:535px;top:10px;display:flex;align-items:center;gap:7px;font-family:'Montserrat',sans-serif;font-weight:700;font-size:8px;letter-spacing:1.2px;color:var(--brand-yellow)}
.lang{left:629px;top:13px;font-family:'Montserrat',sans-serif;font-weight:700;font-size:7px;color:var(--white)}
.search{left:696px;top:11px;width:108px;height:19px;border:1.5px solid var(--brand-yellow);border-radius:10px;font-family:'Montserrat',sans-serif;font-weight:600;font-size:8.5px;letter-spacing:.8px;color:var(--white);padding:3px 0 0 11px}
.search svg{position:absolute;right:9px;top:3px}
.hero-title{left:0;width:874px;top:83px;text-align:center;font-family:'Montserrat',sans-serif;font-weight:800;font-size:19px;letter-spacing:2px;color:var(--white)}
.hero-sub{left:0;width:874px;top:114px;text-align:center;font-family:'Montserrat',sans-serif;font-weight:700;font-size:7.5px;letter-spacing:1px;color:var(--white)}

/* intro */
.chain{left:417px;top:236px}
.section-title{left:0;width:860px;text-align:center;font-weight:900;font-size:23px;letter-spacing:-1px;color:var(--ink)}
.intro-title{top:280px}
.rule{left:403px;top:323px;width:55px;height:2px;background:var(--yellow)}
.intro-text{left:183px;top:342px;width:522px;text-align:center;font-size:13.5px;line-height:16.5px;color:var(--muted)}
.form-title{top:429px}

/* form */
.field{position:absolute;width:264px}
.field .box{height:21px;border:1px solid var(--line);background:var(--white)}
.field .label{margin-top:6px;font-size:7.5px;color:var(--muted)}
.select .box{width:162px;font-size:8px;color:var(--muted);padding:5px 0 0 7px;position:relative}
.select .box svg{position:absolute;right:8px;top:7px}
.message{left:156px;top:661px;width:541px;height:166px;border:1px solid var(--line);font-size:8.5px;color:#a5a5a5;padding:10px 6px}
.send{left:158px;top:854px;width:104px;height:28px;border-radius:14px;background:var(--yellow);color:var(--white);font-weight:700;font-size:7.5px;display:flex;align-items:center;justify-content:center;gap:7px}

/* footer */
.footer{left:0;top:1032px;width:850px;height:168px;background:var(--black);color:var(--white)}
.col{position:absolute;top:30px;font-size:6.3px;line-height:10.5px}
.col h4{font-size:6.5px;font-weight:900;margin-bottom:6px;letter-spacing:.2px}
.col h4 span,.hl{color:var(--brand-yellow)}
.socials{display:flex;gap:5px;margin-top:2px}
.socials i{display:block;width:8px;height:8px;border-radius:2px;background:var(--white)}
.foot-rule{left:179px;top:100px;width:500px;height:1px;background:#777}
.copy{left:179px;top:109px;font-size:5.5px}
</style>
</head>
<body>

<header class="abs hero" role="img" aria-label="Night photo of a lit taxi roof sign on a dark street">
</header>
<div class="abs brand">FAREWAY</div>
<nav class="abs nav">
  <span class="active">HOME</span><span>SHOP</span><span>SERVICES</span><span>INSTALLERS</span><span>CONTACT US</span><span>&nbsp;JOIN US</span>
</nav>
<div class="abs phone">
  <svg width="14" height="14" viewBox="0 0 24 24" fill="none" stroke="#fff" stroke-width="1.6"><path d="M5 3h4l2 5-2.5 1.5a11 11 0 0 0 6 6L16 13l5 2v4a2 2 0 0 1-2 2A17 17 0 0 1 3 5a2 2 0 0 1 2-2z"/><path d="M14 3a7 7 0 0 1 7 7M14 7a3 3 0 0 1 3 3"/></svg>
  <span>555.010.2040</span>
</div>
<div class="abs lang">ENG v</div>
<div class="abs search">search
  <svg width="11" height="11" viewBox="0 0 24 24" fill="none" stroke="#bbb" stroke-width="2"><circle cx="10" cy="10" r="7"/><path d="M15 15l6 6"/></svg>
</div>
<h1 class="abs hero-title">JOIN US</h1>
<p class="abs hero-sub">BE APART OF A WINNING TEAM.</p>

<svg class="abs chain" width="28" height="28" viewBox="0 0 28 28" fill="none" stroke="#f2c53d" stroke-width="1.6">
  <rect x="3" y="10" width="14" height="7" rx="3.5" transform="rotate(-45 10 13.5)"/>
  <rect x="11" y="11" width="14" height="7" rx="3.5" transform="rotate(-45 18 14.5)"/>
</svg>
<h2 class="abs section-title intro-title">There’s strenth in numbers</h2>
<div class="abs rule"></div>
<p class="abs intro-text">Lorem ipsum dolor sit amet, consectetuer adipiscing elit. Aenean commodo ligula eget dolor. Aenean massa. Cum sociis natoque penatibus et magnis dis parturient montes, nascetur ridiculus mus. Donec qu</p>

<h2 class="abs section-title form-title">Fill out the for below to join us.</h2>

<form>
  <div class="field" style="left:158px;top:483px"><div class="box"></div><div class="label">First Name</div></div>
  <div class="field" style="left:435px;top:483px"><div class="box"></div><div class="label">Last Name</div></div>
  <div class="field" style="left:156px;top:545px"><div class="box"></div><div class="label">Email</div></div>
  <div class="field" style="left:435px;top:545px"><div class="box"></div><div class="label">Phone</div></div>
  <div class="field" style="left:156px;top:601px"><div class="box"></div><div class="label">Company Name</div></div>
  <div class="field select" style="left:435px;top:601px"><div class="box">Spain
    <svg width="8" height="7" viewBox="0 0 8 7"><path d="M0 0h8L4 7z" fill="#111"/></svg></div>
    <div class="label">Where on the globe do you reside?</div></div>
  <div class="abs message">Tell us about your company?</div>
  <div class="abs send">Send a Message
    <svg width="11" height="10" viewBox="0 0 24 22" fill="none" stroke="#fff" stroke-width="1.8"><path d="M22 1L1 9l8 3 3 8z"/><path d="M22 1L9 12"/></svg>
  </div>
</form>

<footer class="abs footer">
  <div class="col" style="left:179px;width:115px">
    <h4>ABOUT <span>FAREWAY</span></h4>
    We provide quality dispatch and meter equipment for indecent taxi &amp; fleet vendors.
  </div>
  <div class="col" style="left:307px">
    <h4>CONTACT INFO</h4>
    Shop Office: (555) 014-2290<br>
    Customer service: (555) 0167-3381<br>
    Email: <span class="hl">hello@fareway.example</span>
  </div>
  <div class="col" style="left:435px">
    <h4>HOURS OF SERVICE</h4>
    Monday - Friday: 09:00AM - 09:00PM<br>
    Saturday: 09:00AM - 07:00PM<br>
    Sunday: Closed
  </div>
  <div class="col" style="left:562px">
    <h4>LINK <span>US</span></h4>
    <div class="socials"><i></i><i></i><i></i><i></i><i></i></div>
  </div>
  <div class="abs foot-rule"></div>
  <div class="abs copy">© 2018 <span class="hl">Fareway.example</span> &nbsp;&nbsp;&nbsp;&nbsp;&nbsp;&nbsp; | &nbsp;Trademarks and brands are the property of their respective owners.</div>
</footer>

</body>
</html>
```